Postcard design to acquire new clients for my Property Management Company

I'm looking for a postcard design that I can send to prospective clients detailing information about my company and services.
Postcard should be eye catching and contain information from www.bramblecrestpm.com. I've provided a few screen shots for the most important information and my logo.
Target Market(s)
Real Estate
Industry/Entity Type
Real Estate
Font styles to use
Sans Serif
Requirements
Must have
- Must be eye catching!! this will be a direct mail piece - I'd like for the card to be read and not tossed in the trash immediately.
Design que from the logo.
A place to write / print the receipts name and address.
our physical address - 2387 Hollow Pine Road, Lubbock, TX 79852.
Should not have
- the contact information on the business card is not accurate - please use info from website.

```html
<!DOCTYPE html>
<html lang="en">
<head>
<meta charset="utf-8">
<title>Bramblecrest Property Management Postcard</title>
<link rel="stylesheet" href="https://fonts.googleapis.com/css2?family=Montserrat:wght@400;500;600;700;800&family=Roboto+Condensed:wght@700&display=swap">
<style>
:root{
  --navy:#0f4c8c;
  --navy-deep:#0b3d75;
  --ink:#15376a;
  --sky:#2f8fd6;
  --grey:#c8c9cb;
  --grey-light:#e6e6e7;
  --slate:#6f7275;
  --white:#ffffff;
  --backdrop:#3a3a3c;
}
*{margin:0;padding:0;box-sizing:border-box}
html,body{width:1068px;height:1200px;overflow:hidden}
body{background:var(--backdrop);font-family:"Montserrat",sans-serif;position:relative}
.postcard{position:absolute;left:175px;width:718px;height:468px;background:var(--white);overflow:hidden}
.postcard--front{top:117px}
.postcard--back{top:615px}
.card-shapes{position:absolute;inset:0;width:718px;height:468px}
.abs{position:absolute}
.brand{text-align:center;color:var(--navy);font-weight:600;line-height:1;white-space:nowrap}
.brand__name{display:block;font-size:29px;letter-spacing:6px}
.brand__tag{display:block;font-size:13.5px;letter-spacing:4.6px;margin-top:6px}
.front-brand{left:0;width:718px;top:24px}
.hero-title{left:28px;top:104px;color:var(--white);font-weight:800;font-size:25px;line-height:27px}
.hero-sub{left:28px;top:162px;color:var(--white);font-weight:400;font-size:14.5px;line-height:17px;width:330px}
.feature{left:28px;width:480px;display:flex;gap:12px}
.feature svg{flex:none;width:27px;height:27px;margin-top:2px}
.feature__title{color:var(--white);font-weight:700;font-size:7.8px;line-height:9.4px}
.feature__text{color:var(--white);font-weight:400;font-size:7.8px;line-height:9.4px;width:245px}
.photo-area{position:absolute}
.offer-title{left:24px;top:397px;color:var(--ink);font-weight:800;font-size:16px;letter-spacing:.4px;white-space:nowrap}
.offer-list{left:26px;top:419px;list-style:none;color:var(--ink);font-weight:500;font-size:8.6px;line-height:11.6px}
.offer-list li::before{content:"";display:inline-block;width:0;height:0;border-left:3px solid transparent;border-right:3px solid transparent;border-bottom:6px solid var(--white);margin-right:8px}
.phone{color:var(--ink);font-weight:800;letter-spacing:.5px;line-height:1;white-space:nowrap}
.front-phone{left:348px;top:387px;font-size:45px}
.contact-line{display:flex;gap:12px;font-weight:500;font-size:9.8px;letter-spacing:.3px;align-items:center;white-space:nowrap}
.contact-line span{display:flex;align-items:center;gap:6px}
.contact-line svg{width:10px;height:10px}
.front-contact{left:352px;top:442px;color:var(--white)}
.services-title{left:24px;top:11px;color:var(--navy);font-weight:800;font-size:22.5px;letter-spacing:.3px}
.services-sub{left:26px;top:37px;color:#222;font-weight:400;font-size:10px}
.service{left:24px;width:330px;display:flex;gap:10px}
.service svg{flex:none;width:26px;height:26px;margin-top:2px}
.service__title{color:var(--white);font-weight:700;font-size:7.6px;line-height:9px}
.service__text{color:var(--white);font-weight:400;font-size:7.8px;line-height:9.2px}
.back-phone{left:22px;top:392px;font-size:44px}
.back-contact{left:25px;top:442px;color:var(--ink)}
.postage{left:611px;top:27px;width:76px;height:92px;border:1px solid #9a9a9a;display:flex;align-items:center;justify-content:center;text-align:center;font-family:"Roboto Condensed",sans-serif;font-weight:700;font-size:10.5px;line-height:14px;color:#3b3b3b}
.address-line{left:463px;width:224px;height:1px;background:#9a9a9a}
.back-brand{left:430px;width:270px;top:388px}
.back-brand .brand__name{font-size:23px;letter-spacing:3.6px}
.back-brand .brand__tag{font-size:10.5px;letter-spacing:3.6px;margin-top:5px}
.back-address{left:430px;width:270px;top:434px;text-align:center;color:var(--slate);font-weight:500;font-size:9px;letter-spacing:.3px;white-space:nowrap}
</style>
</head>
<body>

<section class="postcard postcard--front" aria-label="Postcard front">
  <svg class="card-shapes" viewBox="0 0 718 468" aria-hidden="true">
    <defs>
      <linearGradient id="headerFade" x1="0" y1="0" x2="1" y2="0">
        <stop offset="0" stop-color="#ffffff"/><stop offset="1" stop-color="#ececec"/>
      </linearGradient>
      <linearGradient id="greyBand" x1="0" y1="0" x2="0" y2="1">
        <stop offset="0" stop-color="#cfd0d2"/><stop offset="1" stop-color="#aeb0b3"/>
      </linearGradient>
    </defs>
    <rect x="0" y="0" width="718" height="87" fill="url(#headerFade)"/>
    <polygon points="0,87 410,87 298,380 0,380" fill="var(--navy)"/>
    <polygon points="0,87 410,87 361,214 0,214" fill="var(--navy-deep)"/>
    <line x1="424" y1="87" x2="332" y2="300" stroke="var(--navy)" stroke-width="3"/>
    <polygon points="0,380 303,380 334,468 0,468" fill="url(#greyBand)"/>
    <line x1="308" y1="382" x2="336" y2="450" stroke="var(--navy)" stroke-width="3"/>
    <polygon points="340,438 718,438 718,457 346,457" fill="var(--navy)"/>
  </svg>
  <div class="photo-area" role="img" aria-label="Photo of hands holding a small model house with a red roof"
       style="left:305px;top:87px;width:413px;height:293px;clip-path:polygon(123px 0,413px 0,413px 293px,7px 293px);background:linear-gradient(120deg,#cfd4da 0%,#e7d6cf 45%,#e9b9a3 75%,#d9dde2 100%)"></div>

  <div class="abs brand front-brand"><span class="brand__name">BRAMBLECREST</span><span class="brand__tag">PROPERTY MANAGEMENT</span></div>

  <h1 class="abs hero-title">PROPERTY MANAGEMENT<br>ACROSS LUBBOCK, TX</h1>
  <p class="abs hero-sub">Maximize your financial returns with support from our rental specialists</p>

  <div class="abs feature" style="top:229px">
    <svg viewBox="0 0 28 28" fill="none" stroke="#fff" stroke-width="1.4"><circle cx="14" cy="14" r="11" stroke-dasharray="9 3"/><circle cx="14" cy="11" r="3"/><path d="M8 20c1-4 11-4 12 0"/></svg>
    <div><p class="feature__title">Put Our Local Experience to the Test</p><p class="feature__text">Our team has successfully helped countless property owners with their rental home needs. Let us use our experience and know how to get impressive results for you.</p></div>
  </div>
  <div class="abs feature" style="top:275px">
    <svg viewBox="0 0 28 28" fill="none" stroke="#fff" stroke-width="1.4"><circle cx="14" cy="6" r="3.5"/><path d="M8 15c0-4 12-4 12 0"/><path d="M3 14l3 8 5 3M25 14l-3 8-5 3"/></svg>
    <div><p class="feature__title">We Offer Unbeatable Support</p><p class="feature__text">You'll love the hands-on support and attention we provide to our clients. Our goal is to build a mutually beneficial partnership with you &amp; help keep you profitable for the longterm.</p></div>
  </div>
  <div class="abs feature" style="top:321px">
    <svg viewBox="0 0 28 28" fill="none" stroke="#fff" stroke-width="1.4"><rect x="3" y="4" width="22" height="15"/><path d="M10 24h8M14 19v5"/><text x="14" y="15" fill="#fff" stroke="none" font-size="7" text-anchor="middle" font-family="Montserrat,sans-serif">24/7</text></svg>
    <div><p class="feature__title">24/7 Online Portal Access</p><p class="feature__text">Our online account portals provide access to statements, account notes, and more. Sign in at any time to manage your account with us.</p></div>
  </div>

  <h2 class="abs offer-title">GET A FREE RENTAL ANALYSIS</h2>
  <ul class="abs offer-list">
    <li>Determine the rental value of your property.</li>
    <li>Find out how to get the most out of your investment.</li>
    <li>See if your home fits our management approach.</li>
  </ul>

  <p class="abs phone front-phone">(806) 555-0147</p>
  <div class="abs contact-line front-contact">
    <span><svg viewBox="0 0 10 10" fill="none" stroke="#fff" stroke-width="1"><circle cx="5" cy="5" r="4.3"/><path d="M.7 5h8.6M5 .7c2.5 2.5 2.5 6 0 8.6M5 .7c-2.5 2.5-2.5 6 0 8.6"/></svg>www.bramblecrestpm.com</span>
    <span><svg viewBox="0 0 10 10" fill="none" stroke="#fff" stroke-width="1"><rect x=".5" y="2" width="9" height="6.5"/><path d="M.5 2l4.5 3.5L9.5 2"/></svg>info@bramblecrestpm.com</span>
  </div>
</section>

<section class="postcard postcard--back" aria-label="Postcard back">
  <svg class="card-shapes" viewBox="0 0 718 468" aria-hidden="true">
    <rect x="0" y="0" width="370" height="59" fill="var(--grey-light)"/>
    <rect x="0" y="58" width="370" height="2" fill="var(--sky)"/>
    <rect x="0" y="60" width="359" height="320" fill="var(--navy)"/>
    <polygon points="359,60 370,60 359,90" fill="var(--grey-light)"/>
    <polygon points="0,383 362,383 390,468 0,468" fill="#b9babd"/>
    <polygon points="0,438 375,438 380,457 0,457" fill="#f4f4f4"/>
  </svg>

  <h2 class="abs services-title">DISCOVER OUR SERVICES</h2>
  <p class="abs services-sub">We offer full-service property management solutions</p>

  <div class="abs service" style="top:78px">
    <svg viewBox="0 0 26 26" fill="#fff"><path d="M13 3L1 13h3v10h7v-6h4v6h7V13h3z"/></svg>
    <div><p class="service__title">PROPERTY MARKETING</p><p class="service__text">Tired of waiting for weeks on end, hoping to find a new tenant? Let us take over your marketing for you and we'll find a qualified renter quickly.</p></div>
  </div>
  <div class="abs service" style="top:113px">
    <svg viewBox="0 0 26 26" fill="#fff"><circle cx="9" cy="8" r="4"/><circle cx="18" cy="9" r="3.3"/><path d="M2 21c0-6 14-6 14 0zM15 21c0-2 0-4-1-5 4-2 11-1 11 5z"/></svg>
    <div><p class="service__title">TENANT SCREENING</p><p class="service__text">We don't just find someone to rent your home—we find the best renters. We screen all applications using fair housing guidelines to protect you.</p></div>
  </div>
  <div class="abs service" style="top:148px">
    <svg viewBox="0 0 26 26"><text x="13" y="22" fill="#fff" font-size="24" font-weight="700" text-anchor="middle" font-family="Montserrat,sans-serif">$</text></svg>
    <div><p class="service__title">RENT COLLECTION</p><p class="service__text">Stop guessing when you'll receive your rental earnings every month and say hello to consistent payments. We keep your tenants current.</p></div>
  </div>
  <div class="abs service" style="top:183px">
    <svg viewBox="0 0 26 26" fill="#fff"><path d="M11 4l8 0 3 4-6 2-2-2z"/><path d="M13 9l2 2-10 12-2-2z"/></svg>
    <div><p class="service__title">MAINTENANCE</p><p class="service__text">Still scrambling to respond to repair requests every time you receive a tenant call? Let us coordinate repair work on your behalf!</p></div>
  </div>
  <div class="abs service" style="top:219px">
    <svg viewBox="0 0 26 26" fill="none" stroke="#fff" stroke-width="3"><circle cx="11" cy="11" r="7"/><path d="M16 16l7 7"/></svg>
    <div><p class="service__title">PROPERTY INSPECTIONS</p><p class="service__text">Inspections form an important part of our proactive property manage-ment approach. We visit every home in our portfolio regularly.</p></div>
  </div>
  <div class="abs service" style="top:256px">
    <svg viewBox="0 0 26 26" fill="#fff"><path d="M2 3h1.6v19H24v1.6H2z"/><rect x="7" y="13" width="2" height="7"/><rect x="11" y="9" width="2" height="11"/><rect x="15" y="14" width="2" height="6"/><rect x="19" y="7" width="2" height="13"/></svg>
    <div><p class="service__title">FINANCIAL REPORTING</p><p class="service__text">Keep a handle on your real estate performance. We generate monthly statements so you can review income &amp; expenses at a moment's notice.</p></div>
  </div>
  <div class="abs service" style="top:293px">
    <svg viewBox="0 0 26 26" fill="#fff"><path d="M13 2l9 3v7c0 6-4 10-9 12-5-2-9-6-9-12V5z"/><path d="M13 5v16c-3-1.5-6-4.5-6-9V7z" fill="var(--navy)"/></svg>
    <div><p class="service__title">EVICTIONS</p><p class="service__text">When things go wrong inside your rental home, rest easy with the experts on your side. We will handle evictions for you &amp; find new renters when its over.</p></div>
  </div>
  <div class="abs service" style="top:339px">
    <svg viewBox="0 0 26 26" fill="none" stroke="#fff" stroke-width="1.8"><path d="M13 3v19M7 22h12M4 7h18"/><path d="M4 7l-3 8h6zM22 7l-3 8h6z"/></svg>
    <div><p class="service__title">LEGAL GUIDANCE</p><p class="service__text">Don't accidentally violate one of the many ordinances and housing laws governing your relationship with your tenants. Let us keep you compliant.</p></div>
  </div>

  <p class="abs phone back-phone">(806) 555-0147</p>
  <div class="abs contact-line back-contact">
    <span><svg viewBox="0 0 10 10" fill="none" stroke="var(--ink)" stroke-width="1"><circle cx="5" cy="5" r="4.3"/><path d="M.7 5h8.6M5 .7c2.5 2.5 2.5 6 0 8.6M5 .7c-2.5 2.5-2.5 6 0 8.6"/></svg>www.bramblecrestpm.com</span>
    <span><svg viewBox="0 0 10 10" fill="none" stroke="var(--ink)" stroke-width="1"><rect x=".5" y="2" width="9" height="6.5"/><path d="M.5 2l4.5 3.5L9.5 2"/></svg>info@bramblecrestpm.com</span>
  </div>

  <div class="abs postage">PRSRTSTD<br>ECRWSS<br>U.S.POSTAGE<br>PAID</div>
  <div class="abs address-line" style="top:211px"></div>
  <div class="abs address-line" style="top:257px"></div>
  <div class="abs address-line" style="top:298px"></div>
  <div class="abs address-line" style="top:343px"></div>

  <div class="abs brand back-brand"><span class="brand__name">BRAMBLECREST</span><span class="brand__tag">PROPERTY MANAGEMENT</span></div>
  <p class="abs back-address">2387 Hollow Pine Road, Lubbock, TX 79852</p>
</section>

</body>
</html>
```